TALMORK

The business want a professional looking business card. We have a scetch we will add but want the extra upgrade, and would like more suggestions for variations of our business cards.

```html
<!DOCTYPE html>
<html lang="en">
<head>
<meta charset="utf-8">
<title>TALMORK — Business Card</title>
<link rel="stylesheet" href="https://fonts.googleapis.com/css2?family=Cinzel:wght@500;600&family=Tinos:wght@700&family=Poppins:wght@400&display=swap">
<style>
  :root {
    --page-bg: #dcdcdc;
    --card-light: #5b1a1f;
    --card-mid: #4a1519;
    --card-dark: #260b0e;
    --gold: #d2ae55;
    --gold-soft: #c9a24a;
    --icon-fill: #ecd7a6;
    --icon-ink: #5a1a1e;
  }
  * { margin: 0; padding: 0; box-sizing: border-box; }
  html, body {
    width: 1200px; height: 2281px; overflow: hidden;
    background: var(--page-bg);
  }
  .canvas { position: relative; width: 1200px; height: 2281px; }
  .card {
    position: absolute; left: 102px; width: 995px; height: 568px;
    background: linear-gradient(120deg, var(--card-light) 0%, var(--card-mid) 55%, var(--card-dark) 100%);
    box-shadow: 0 6px 14px rgba(0,0,0,0.25);
    overflow: hidden;
  }
  .card--front { top: 537px; }
  .card--back { top: 1175px; }

  .wordmark {
    position: absolute; color: var(--gold);
    font-family: "Cinzel", "Times New Roman", serif; font-weight: 500;
    text-align: center; white-space: nowrap; line-height: 1;
  }
  .tagline {
    position: absolute; color: var(--gold-soft);
    font-family: "Poppins", Arial, sans-serif; font-weight: 400;
    text-align: center; white-space: nowrap; line-height: 1;
  }
  .card--front .wordmark { left: 451px; width: 500px; top: 258px; font-size: 57px; letter-spacing: 0.3em; text-indent: 0.3em; }
  .card--front .tagline { left: 551px; width: 300px; top: 328px; font-size: 20px; letter-spacing: 0.4em; text-indent: 0.4em; }

  .brand-dot {
    position: absolute; left: 186px; top: 165px; width: 60px; height: 60px;
    border-radius: 50%; background: var(--gold);
  }
  .card--back .wordmark { left: 56px; width: 320px; top: 352px; font-size: 44px; letter-spacing: 0.22em; text-indent: 0.22em; }
  .card--back .tagline { left: 66px; width: 300px; top: 409px; font-size: 16px; letter-spacing: 0.42em; text-indent: 0.42em; }

  .divider { position: absolute; left: 423px; top: 142px; width: 2px; height: 301px; background: var(--gold); }

  .person-name {
    position: absolute; left: 462px; top: 146px;
    font-family: "Tinos", "Times New Roman", serif; font-weight: 700;
    font-size: 44px; color: var(--gold); white-space: nowrap; line-height: 1;
  }
  .person-role {
    position: absolute; left: 462px; top: 205px;
    font-family: "Poppins", Arial, sans-serif; font-size: 31px;
    color: var(--icon-fill); white-space: nowrap; line-height: 1;
  }
  .role-rule { position: absolute; left: 462px; top: 256px; width: 50px; height: 1px; background: var(--gold); }

  .contact-list { position: absolute; left: 462px; top: 296px; list-style: none; }
  .contact-item {
    display: flex; align-items: center; height: 26px; margin-bottom: 25px;
    font-family: "Poppins", Arial, sans-serif; font-size: 29px;
    color: var(--icon-fill); white-space: nowrap;
  }
  .contact-icon { width: 26px; height: 26px; margin-right: 16px; flex: none; }
</style>
</head>
<body>
<main class="canvas">

  <section class="card card--front" aria-label="Card front">
    <div class="wordmark">TALMORK</div>
    <div class="tagline">SINCE 2026</div>
  </section>

  <section class="card card--back" aria-label="Card back">
    <div class="brand-dot"></div>
    <div class="wordmark">TALMORK</div>
    <div class="tagline">SINCE 2026</div>

    <div class="divider"></div>

    <h1 class="person-name">Henrik Solberg Aas</h1>
    <p class="person-role">CEO &amp; Founder</p>
    <div class="role-rule"></div>

    <ul class="contact-list">
      <li class="contact-item">
        <svg class="contact-icon" viewBox="0 0 26 26" aria-hidden="true">
          <circle cx="13" cy="13" r="13" fill="var(--icon-fill)"/>
          <path d="M8.5 7.5c.8-.8 1.6-.6 2 .1l1.2 2c.3.6.1 1.1-.4 1.5l-.8.6c.6 1.4 1.8 2.6 3.2 3.2l.6-.8c.4-.5.9-.7 1.5-.4l2 1.2c.7.4.9 1.2.1 2l-1 1c-1 1-4 .2-6.5-2.3S6.5 9.5 7.5 8.5z" fill="var(--icon-ink)"/>
        </svg>
        004791234567
      </li>
      <li class="contact-item">
        <svg class="contact-icon" viewBox="0 0 26 26" aria-hidden="true">
          <circle cx="13" cy="13" r="13" fill="var(--icon-fill)"/>
          <rect x="7" y="8.5" width="12" height="9" rx="1.2" fill="none" stroke="var(--icon-ink)" stroke-width="1.4"/>
          <path d="M7.5 9.5l5.5 4 5.5-4" fill="none" stroke="var(--icon-ink)" stroke-width="1.4"/>
        </svg>
        talmork.llc@mailpost.com
      </li>
      <li class="contact-item">
        <svg class="contact-icon" viewBox="0 0 26 26" aria-hidden="true">
          <circle cx="13" cy="13" r="13" fill="var(--icon-fill)"/>
          <g fill="none" stroke="var(--icon-ink)" stroke-width="1.2">
            <circle cx="13" cy="13" r="6.5"/>
            <ellipse cx="13" cy="13" rx="2.8" ry="6.5"/>
            <path d="M6.5 13h13M7.5 10h11M7.5 16h11"/>
          </g>
        </svg>
        www.talmork.llc
      </li>
    </ul>
  </section>

</main>
</body>
</html>
```